Business Card Design

We are a residential half way house for the addict ,the alcoholic and dual diagnosed in recovery.
i house both men and woman age 18+

Industry/Entity Type

Residential

```html
<!DOCTYPE html>
<html lang="en">
<head>
<meta charset="utf-8">
<title>Meredith's Family Sober House – Business Card</title>
<link rel="stylesheet" href="https://fonts.googleapis.com/css2?family=Exo+2:wght@400;500;700&display=swap">
<style>
  :root {
    --stage: #e9e6e1;
    --card: #000000;
    --ink: #ffffff;
    --rule: #f2f2f2;
    --glow-pink: #e2307a;
    --glow-magenta: #c13bd0;
    --glow-blue: #3fb6e8;
    --glow-orange: #f28a2e;
    --glow-green: #3c8f4a;
  }
  * { box-sizing: border-box; margin: 0; padding: 0; }
  html, body {
    width: 1200px; height: 885px; overflow: hidden;
    background: var(--stage);
    font-family: "Exo 2", "Segoe UI", sans-serif;
  }
  .card {
    position: absolute;
    left: 380px; top: 57px;
    width: 440px; height: 770px;
    background: var(--card);
    color: var(--ink);
    overflow: hidden;
    border-radius: 4px;
    box-shadow: 0 10px 30px rgba(0,0,0,.25);
  }
  .card__artwork {
    position: absolute; left: 0; top: 0;
    width: 440px; height: 440px;
    background:
      radial-gradient(ellipse 55% 40% at 50% 48%, var(--glow-blue) 0%, rgba(63,182,232,0) 70%),
      radial-gradient(ellipse 75% 55% at 45% 45%, var(--glow-pink) 0%, var(--glow-magenta) 35%, rgba(193,59,208,0) 70%),
      radial-gradient(ellipse 40% 30% at 85% 25%, var(--glow-orange) 0%, rgba(242,138,46,0) 70%),
      radial-gradient(ellipse 40% 30% at 15% 20%, var(--glow-green) 0%, rgba(60,143,74,0) 70%),
      #0a0a14;
  }
  .card__artwork::after {
    content: "";
    position: absolute; left: 0; right: 0; bottom: 0; height: 170px;
    background: linear-gradient(to bottom, rgba(0,0,0,0), var(--card) 85%);
  }
  .call {
    position: absolute; top: 22px; left: 0; right: 0;
    display: flex; justify-content: center; align-items: flex-start; gap: 12px;
  }
  .call__label { font-size: 36px; font-weight: 700; line-height: 1; }
  .call__numbers { font-size: 22px; font-weight: 500; line-height: 1.05; }
  .details {
    position: absolute; left: 0; right: 0; top: 445px;
    text-align: center;
  }
  .company__name { font-size: 35px; font-weight: 700; line-height: 1; }
  .company__type { font-size: 23px; font-weight: 700; line-height: 1.05; }
  .person { margin-top: 22px; }
  .person__name { font-size: 34px; font-weight: 700; line-height: 1; }
  .person__role { font-size: 23px; font-weight: 700; line-height: 1.05; }
  .contact { margin-top: 14px; font-size: 23px; font-weight: 500; line-height: 1.15; }
  .contact__fax { font-weight: 700; }
  .rule {
    width: 370px; height: 4px; margin: 10px auto 12px;
    background: var(--rule);
  }
  .address { font-size: 23px; font-weight: 400; line-height: 1.2; }
</style>
</head>
<body>
  <article class="card">
    <div class="card__artwork" role="img" aria-label="Illustration of a crowd in silhouette celebrating with raised arms against colourful glowing lights and music notes"></div>

    <div class="call">
      <span class="call__label">Call</span>
      <span class="call__numbers">(555) 014-2270<br>(555) 014-2271</span>
    </div>

    <section class="details">
      <div class="company">
        <p class="company__name">Meredith's Family</p>
        <p class="company__type">Sober House Inc.</p>
      </div>
      <div class="person">
        <p class="person__name">Dana Whitfield</p>
        <p class="person__role">Owner</p>
      </div>
      <div class="contact">
        <p class="contact__fax">fax (555) 014-3398</p>
        <p class="contact__email">danawhitfield@example.com</p>
      </div>
      <div class="rule"></div>
      <p class="address">418 Palm Grove Rd. Harbor City<br>Fla 30000</p>
    </section>
  </article>
</body>
</html>
```